New design for Comparison website

We need new design for our website https://prisvaktposten.no/ . We compare prices and providers in different niches such as electricity, mobile plans, broadband etc.

We would like to see design like Tarivo com or our competitor kjøpklokt no

We will need design of all pages, with tables, tables are somewhat different depending on the service compared (use kjøpklokt no for reference) . Our focus is CTR through comparison Tables.

Final design must communicate following: Professionalism, thrust, authority.

Number of Pages Required

5+ page

Font styles to use
Sans Serif

Colors

Designer to choose colors to be used in the design.

Requirements
Must have
• Tables
Nice to have
• Images in content

```html
<!DOCTYPE html>
<html lang="no">
<head>
<meta charset="utf-8">
<title>Prisvaktposten – Sammenlign leverandører</title>
<link href="https://fonts.googleapis.com/css2?family=Open+Sans:wght@400;600;700;800&display=swap" rel="stylesheet">
<style>
:root{
  --green:#14a37a;
  --green-dark:#0f8a66;
  --ink:#1c1c1c;
  --text:#444;
  --muted:#8a8a8a;
  --dark:#444444;
  --footer:#4a4a4a;
  --light:#f4f4f4;
  --white:#fff;
}
*{box-sizing:border-box;margin:0;padding:0}
html,body{width:1200px;height:2406px;overflow:hidden}
body{font-family:"Open Sans",Arial,sans-serif;color:var(--text);background:var(--white);position:relative}
.abs{position:absolute}

/* header */
.site-header{position:absolute;left:0;top:0;width:1200px;height:112px;background:var(--white)}
.brand{position:absolute;left:132px;top:38px;display:flex;align-items:center;gap:12px}
.brand-mark{width:40px;height:40px;background:var(--green)}
.brand-name{font-weight:700;font-size:29px;color:var(--green);letter-spacing:-.5px}
.util-nav{position:absolute;right:133px;top:26px;font-size:11px;color:#666;display:flex;gap:9px}
.util-nav span.sep{color:#aaa}
.main-nav{position:absolute;right:133px;top:67px;display:flex;gap:33px;font-size:13.5px;font-weight:700;color:var(--ink);text-transform:uppercase}
.main-nav .active{color:var(--green)}

/* hero */
.hero{position:absolute;left:0;top:112px;width:1200px;height:502px;background:linear-gradient(120deg,#b9c3cc 0%,#e3e7ea 40%,#eef0f1 70%,#dfe3e6 100%)}
.hero-left{position:absolute;left:0;top:0;width:600px;height:502px;background:rgba(120,130,140,.25)}
.hero-arrow{position:absolute;top:237px;width:28px;height:28px;border-radius:50%;background:rgba(120,120,120,.55)}
.hero h1,.hero h2{font-size:29px;font-weight:800;color:var(--ink);line-height:1.15;text-transform:uppercase}
.hero p{font-size:16.5px;color:var(--ink);line-height:1.3}
.btn-start{position:absolute;left:132px;top:286px;width:120px;height:51px;background:var(--green);color:#fff;font-weight:700;font-size:22px;display:flex;align-items:center;justify-content:center}
.search{position:absolute;left:651px;top:286px;width:416px;height:51px;background:#fff;display:flex;align-items:center;padding:0 22px;font-size:13px;color:#777;justify-content:space-between;box-shadow:0 1px 3px rgba(0,0,0,.1)}

/* how it works */
.section-title{position:absolute;left:0;width:1200px;text-align:center;color:var(--green);font-weight:700;font-size:32px;text-transform:uppercase}
.step{position:absolute;top:759px;width:300px;text-align:center}
.step-icon{position:relative;margin:0 auto;width:80px;height:80px;background:var(--green);display:flex;align-items:center;justify-content:center}
.step-num{position:absolute;left:0;top:0;width:16px;height:16px;background:var(--green-dark);color:#fff;font-size:10px;line-height:16px}
.step h3{margin-top:28px;font-size:21px;font-weight:400;color:var(--green)}
.step h4{margin-top:6px;font-size:15px;font-weight:400;color:var(--ink)}
.step p{margin-top:8px;font-size:11px;color:var(--muted);line-height:1.45}

/* categories */
.cat-band{position:absolute;left:0;top:1023px;width:1200px;height:369px;background:linear-gradient(180deg,#aab3ba 0%,#d5dade 45%,#c2c8cc 100%)}
.cat-tile{position:absolute;top:1104px;width:176px;height:208px}
.cat-photo{width:176px;height:170px}
.cat-label{height:38px;background:var(--green);color:#fff;font-size:12px;font-weight:700;text-transform:uppercase;display:flex;align-items:center;justify-content:center}
.cat-pointer{position:absolute;left:207px;top:1312px;width:0;height:0;border-left:13px solid transparent;border-right:13px solid transparent;border-top:13px solid var(--green)}

/* comparison */
.compare{position:absolute;left:0;top:1392px;width:1200px;height:517px;background:var(--light)}
.cmp-table{position:absolute;left:132px;top:1525px;width:935px;height:304px;display:grid;grid-template-columns:251px 217px 216px 251px}
.cmp-col{display:flex;flex-direction:column}
.cmp-head{height:97px;background:var(--dark);color:#fff;font-size:16px;display:flex;flex-direction:column;justify-content:center;padding-left:80px;gap:8px;border-right:1px solid #555}
.cmp-col:nth-child(n+2) .cmp-head{padding-left:48px}
.provider{display:flex;align-items:center;gap:7px;font-weight:700;font-size:15px}
.provider i{display:inline-block;width:22px;height:22px;border-radius:50%;background:#bbb}
.cmp-price{height:123px;background:#fff;border-right:1px solid #eee;padding:26px 0 0 80px;color:var(--ink);font-size:20px;line-height:1.2}
.cmp-col:nth-child(n+2) .cmp-price{padding-left:48px}
.cmp-price small{display:block;margin-top:4px;font-size:12px;color:var(--muted)}
.cmp-action{margin-top:3px;height:81px;background:#fff;border-right:1px solid #eee;display:flex;align-items:center;justify-content:center}
.btn-order{width:120px;height:43px;background:var(--green);color:#fff;font-size:15px;font-weight:600;display:flex;align-items:center;justify-content:center}
.cmp-arrow{position:absolute;top:1566px}

/* newsletter */
.news-sub{position:absolute;left:0;top:2026px;width:1200px;text-align:center;font-size:20px;color:var(--green)}
.news-input{position:absolute;left:342px;top:2061px;width:516px;height:51px;background:#f4f4f4;border:1px solid #d8d8d8;display:flex;align-items:center;justify-content:space-between;padding:0 20px 0 22px;font-size:12px;color:#777}

/* footer */
.site-footer{position:absolute;left:0;top:2193px;width:1200px;height:213px;background:var(--footer);color:#ddd;font-size:11px}
.foot-list{position:absolute;top:48px;list-style:none;line-height:21px}
.foot-list li::before{content:"•";margin-right:6px;color:#aaa}
.copy{position:absolute;left:576px;top:46px;line-height:21px}
.foot-brand{position:absolute;left:576px;top:116px;display:flex;align-items:center;gap:10px;font-weight:700;font-size:22px;color:#9a9a9a}
.foot-brand span.sq{width:30px;height:30px;background:#9a9a9a}
.social{position:absolute;top:48px;width:35px;height:35px;background:#6b6b6b}
</style>
</head>
<body>

<header class="site-header">
  <div class="brand"><span class="brand-mark"></span><span class="brand-name">Prisvaktposten</span></div>
  <nav class="util-nav"><span>Hjem</span><span class="sep">|</span><span>Om oss</span><span class="sep">|</span><span>Kontakt</span><span class="sep">|</span><span>Vilkår</span><span class="sep">|</span><span>Personvern</span><span class="sep">|</span><span>Informasjonskapsler</span></nav>
  <nav class="main-nav"><span class="active">Bredbånd</span><span>Mobilabonnement</span><span>Strøm</span><span>Webhotell og domener</span><span>Boligalarm</span></nav>
</header>

<section class="hero">
  <div class="abs" role="img" aria-label="Hender som skriver på en bærbar datamaskin på et lyst kontorbord" style="inset:0"></div>
  <div class="hero-left"></div>
  <div class="hero-arrow" style="left:23px"></div>
  <div class="hero-arrow" style="left:1147px"></div>
  <div class="abs" style="left:132px;top:158px;width:460px">
    <h1>Se gjennom<br>tilgjengelige kategorier</h1>
    <p style="margin-top:3px">Begynn å undersøke og sammenlign leverandørene for de tjenestene du trenger.</p>
  </div>
  <div class="btn-start">START</div>
  <div class="abs" style="right:133px;top:158px;width:500px;text-align:right">
    <h2>Den som leter,<br>skal finne</h2>
    <p style="margin-top:3px">Se om du benytter den beste leverandøren av tjenester</p>
  </div>
  <div class="search"><span>Skriv inn tjenester</span>
    <svg width="22" height="22" viewBox="0 0 22 22"><circle cx="9" cy="9" r="6.5" fill="none" stroke="#14a37a" stroke-width="3"/><line x1="14" y1="14" x2="20" y2="20" stroke="#14a37a" stroke-width="3.5" stroke-linecap="round"/></svg>
  </div>
</section>

<h2 class="section-title" style="top:684px">Hvordan vår side fungerer</h2>

<div class="step" style="left:124px">
  <div class="step-icon"><span class="step-num">1</span>
    <svg width="34" height="28" viewBox="0 0 34 28" fill="#fff"><rect x="0" y="1" width="6" height="6"/><rect x="10" y="2" width="24" height="4"/><rect x="0" y="11" width="6" height="6"/><rect x="10" y="12" width="24" height="4"/><rect x="0" y="21" width="6" height="6"/><rect x="10" y="22" width="24" height="4"/></svg>
  </div>
  <h3>Velg Kategori</h3><h4>Les mer om tjenesten</h4>
  <p>Vi samler mest relevant informasjon om tjenesten på et<br>sted slik at du lærer det viktigste på kort tid.</p>
</div>
<div class="step" style="left:448px">
  <div class="step-icon"><span class="step-num">2</span>
    <svg width="32" height="34" viewBox="0 0 32 34" fill="none" stroke="#fff" stroke-width="3"><path d="M3 9h12v22H3z"/><path d="M12 3h10l7 7v16H17"/><path d="M22 3v7h7"/></svg>
  </div>
  <h3>Sammenlign Leverandører</h3><h4>Velg mellom de beste og mest pålitelige.</h4>
  <p>De beste og mest seriøse aktører sammenlignet slik at du<br>kan velge den som passer deg best.</p>
</div>
<div class="step" style="left:772px">
  <div class="step-icon"><span class="step-num">3</span>
    <svg width="30" height="30" viewBox="0 0 30 30" fill="none" stroke="#fff" stroke-width="3.5"><circle cx="15" cy="15" r="12"/><path d="M9 15l4.5 4.5L21 11"/></svg>
  </div>
  <h3>Bestill Tjenesten</h3><h4>Bestill den beste leverandøren</h4>
  <p>Bestill tjenesten og nyt at du har fått den beste lever-<br>andøren enkelt og raskt.</p>
</div>

<section class="cat-band" role="img" aria-label="Person som jobber ved en bærbar datamaskin, dempet bakgrunnsbilde"></section>
<div class="cat-tile" style="left:132px"><div class="cat-photo" role="img" aria-label="Glasskule på et tastatur" style="background:linear-gradient(160deg,#2f5e86,#9fc4de 55%,#3b6d95)"></div><div class="cat-label">Bredbånd</div></div>
<div class="cat-tile" style="left:322px"><div class="cat-photo" role="img" aria-label="Hånd som holder en smarttelefon" style="background:linear-gradient(160deg,#e9e4dd,#a8a39d 50%,#6a6f7a)"></div><div class="cat-label">Mobilabonnement</div></div>
<div class="cat-tile" style="left:512px"><div class="cat-photo" role="img" aria-label="Tent bordlampe på et nattbord" style="background:linear-gradient(160deg,#e8e0b8,#f4eed8 45%,#7c8c54)"></div><div class="cat-label">Strøm</div></div>
<div class="cat-tile" style="left:702px"><div class="cat-photo" role="img" aria-label="Lysende lyspære foran nettadresse på en tavle" style="background:radial-gradient(circle at 55% 40%,#f4c531,#7a6a2a 35%,#2a2d33 70%)"></div><div class="cat-label">Webhotell og domener</div></div>
<div class="cat-tile" style="left:892px"><div class="cat-photo" role="img" aria-label="Person som betjener et alarmpanel hjemme" style="background:linear-gradient(160deg,#dfe3e6,#b8c4cf 55%,#8aa0b5)"></div><div class="cat-label">Boligalarm</div></div>
<div class="cat-pointer"></div>

<section class="compare"></section>
<h2 class="section-title" style="top:1467px">Bredbånd sammenligning 2017</h2>
<div class="cmp-table">
  <div class="cmp-col">
    <div class="cmp-head"><span class="provider"><i style="background:#e2463c"></i>Nettlinje</span><span>20 / 1 Mbit/s</span></div>
    <div class="cmp-price">3 588 kr<br>Årlig kostnad<small>(299 kr pr mnd)</small></div>
    <div class="cmp-action"><span class="btn-order">ORDER NOW</span></div>
  </div>
  <div class="cmp-col">
    <div class="cmp-head"><span class="provider"><i style="background:#3fa86a"></i>FiberNord</span><span>10 / 1 Mbit/s</span></div>
    <div class="cmp-price">3 876 kr<br>Årlig kostnad<small>(323 kr pr mnd)</small></div>
    <div class="cmp-action"><span class="btn-order">ORDER NOW</span></div>
  </div>
  <div class="cmp-col">
    <div class="cmp-head"><span class="provider"><i></i></span><span>20 / 1 Mbit/s</span></div>
    <div class="cmp-price">3 876 kr<br>Årlig kostnad<small>(323 kr pr mnd)</small></div>
    <div class="cmp-action"><span class="btn-order">ORDER NOW</span></div>
  </div>
  <div class="cmp-col">
    <div class="cmp-head"><span class="provider"><i></i></span><span>60 / 15 Mbit/s</span></div>
    <div class="cmp-price">4 788 kr<br>Årlig kostnad<small>(399 kr pr mnd)</small></div>
    <div class="cmp-action"><span class="btn-order">ORDER NOW</span></div>
  </div>
</div>
<svg class="cmp-arrow" style="left:154px" width="12" height="18" viewBox="0 0 12 18"><path d="M10 2L3 9l7 7" fill="none" stroke="#fff" stroke-width="3"/></svg>
<svg class="cmp-arrow" style="left:1032px" width="12" height="18" viewBox="0 0 12 18"><path d="M2 2l7 7-7 7" fill="none" stroke="#fff" stroke-width="3"/></svg>

<h2 class="section-title" style="top:1983px">Abonner på vårt nyhetsbrev</h2>
<p class="news-sub">Få Nyheter og tilbud levert direkte til din innboks.</p>
<div class="news-input"><span>Email Address</span>
  <svg width="24" height="18" viewBox="0 0 24 18"><rect width="24" height="18" rx="2" fill="#14a37a"/><path d="M2 3l10 7 10-7" fill="none" stroke="#fff" stroke-width="2"/></svg>
</div>

<footer class="site-footer">
  <ul class="foot-list" style="left:132px"><li>Hjem</li><li>Om oss</li><li>Kontakt</li><li>Vilkår</li><li>Personvern</li><li>Informasjonskapsler</li></ul>
  <ul class="foot-list" style="left:300px"><li>Bredbånd</li><li>Mobilabonnement</li><li>Strøm</li><li>Webhotell og Domener</li><li>Boligalarm</li></ul>
  <div class="copy">Copyright © 2017 Prisvaktposten.no.<br>All rights reserved.</div>
  <div class="foot-brand"><span class="sq"></span>Prisvaktposten</div>
  <div class="social" style="left:935px"></div>
  <div class="social" style="left:984px"></div>
  <div class="social" style="left:1032px"></div>
</footer>

</body>
</html>
```